Creation of brand identity and website "Tandem K"

I am currently seeking an brand, identity and web design for a new project called Tandem K. This is a brand new concept from scratch and you have free-reign on the whole design process, taking into account my preference below.

Must include the name "Tandem K", or "Tandem K: Or the year I woke Up". Kudos is this forms part of the brands logo

Design that can be easily scaled to potentially include: a blog, timeline and vlogs.

Minimal but effective use of colour (however any colours and combinations permitted

Use of icons/graphics over text wherever possible

Minimal use of frames and borders

I appreciate this is a fairly wide scope so please contact me on marblefinch@postwillow.com with any questions or more information on what the project is.

Target Market(s)

Male and Female 20-40
Blog readers
Selfhelp

Industry/Entity Type

Seeking

Number of Pages Required

1 page

Font styles to use
Serif
Sans Serif

Requirements
Must have
• It is in effect a blog design, so about me section, recent blog / archived posts, reader comments / Q and A section.
• A coded design would be appreciated to make my life easier however I have left the design as uncoded as getting the right design matters more to me and I want to keep the project open to as many designers as possible
Nice to have
• See project description for other details and please ask if you need anything else :)
Should not have
• Mustn't be cluttered or feel fussy
• Promote icons over text
• Frames / multiple borders

```html
<!DOCTYPE html>
<html lang="en">
<head>
<meta charset="utf-8">
<title>Tandem K</title>
<link href="https://fonts.googleapis.com/css2?family=Roboto+Condensed:wght@400;700&family=Lato:ital,wght@0,400;0,700;1,700&display=swap" rel="stylesheet">
<style>
:root{
  --navy:#253a5e;
  --navy-dark:#1f2f4d;
  --gold:#f4b41a;
  --page:#f5f5f5;
  --card:#ffffff;
  --line:#dcdcdc;
  --text:#555;
  --blue:#1b75bb;
  --red:#e4473b;
  --sky:#27a9e1;
  --grey:#6b6b6b;
}
*{box-sizing:border-box;margin:0;padding:0}
html,body{width:700px;height:1200px;overflow:hidden}
body{background:var(--page);font-family:"Lato",sans-serif;color:var(--text);position:relative}

/* header */
.site-header{position:absolute;left:0;top:0;width:700px;height:40px;background:#fff;border-bottom:2px solid #d0d0d0}
.brand{position:absolute;left:76px;top:0;font:400 19px/38px "Roboto Condensed",sans-serif;color:var(--navy)}
.nav a{position:absolute;top:0;height:38px;font:400 10px/38px "Roboto Condensed",sans-serif;color:var(--navy);text-decoration:none}
.nav a.active{background:var(--navy);color:#fff;border-bottom:3px solid var(--gold);padding:0 9px;height:41px;line-height:38px}

/* main column */
.section-bar{position:absolute;left:77px;top:74px;width:361px;height:19px;background:var(--navy);color:#fff;font:400 12.5px/19px "Roboto Condensed",sans-serif;padding-left:8px}
.section-bar svg{position:absolute;right:6px;top:4px}
.post{position:absolute;left:77px;width:361px;height:146px;background:var(--card);border:1px solid var(--line);box-shadow:0 0 0 3px #fff inset}
.post .thumb{position:absolute;left:8px;top:11px;width:134px;height:121px;border:2px solid #e6e6e6}
.post h2{position:absolute;left:154px;top:9px;font:400 11.5px/14px "Roboto Condensed",sans-serif;color:var(--navy)}
.post .meta{position:absolute;left:154px;top:27px;width:198px;border-top:1px solid #e4e4e4;padding-top:7px;font:400 7px/9px "Lato",sans-serif;color:#555;display:flex;align-items:center;gap:5px}
.meta .dot{width:6px;height:5px;background:var(--gold);border-radius:1px}
.meta .bubble{width:7px;height:5px;background:var(--gold);border-radius:3px}
.meta .sep{width:1px;height:10px;background:#999;margin:0 4px}
.post p{position:absolute;left:154px;top:56px;width:200px;font:400 7px/12px "Lato",sans-serif;color:#555}
.counts{position:absolute;left:154px;top:99px;display:flex;gap:6px}
.count{width:26px}
.count b{display:block;height:18px;border:1px solid;border-radius:2px;text-align:center;font:400 7px/16px "Lato",sans-serif;background:#fff}
.count i{display:block;margin-top:3px;height:9px;font:700 5.5px/7px "Lato",sans-serif;font-style:normal;text-align:center;border:1px solid #ccc;border-radius:1px;color:#555}
.c1 b{border-color:var(--blue);color:var(--blue)} .c1 i{background:var(--blue);color:#fff;border-color:var(--blue)}
.c2 b{border-color:var(--red);color:var(--red)} .c2 i{color:var(--red)}
.c3 b{border-color:var(--sky);color:var(--sky)} .c3 i{color:var(--navy)}
.c4 b{border-color:#888;color:#555}
.share{position:absolute;left:310px;top:95px;font:400 7px/9px "Lato",sans-serif;color:#666;display:flex;gap:4px;align-items:center}
.btn{display:inline-block;background:var(--navy);color:#fff;font:400 8px/20px "Roboto Condensed",sans-serif;text-align:center;border-radius:2px}
.post .btn{position:absolute;left:292px;top:113px;width:58px;height:21px;line-height:21px}
.load-more{position:absolute;left:77px;top:918px;width:361px;height:24px;background:var(--gold);color:var(--navy);font:400 8px/24px "Roboto Condensed",sans-serif;text-align:center}
.load-more svg{vertical-align:-2px;margin-right:5px}

/* sidebar */
.widget{position:absolute;left:450px;width:173px;background:#fff;border:1px solid var(--line)}
.widget h3{font:400 11px/14px "Roboto Condensed",sans-serif;color:var(--navy)}
.newsletter{top:74px;height:85px;padding:7px 8px}
.newsletter .field{margin-top:8px;height:21px;border:1px solid #ddd;font:400 6.5px/19px "Lato",sans-serif;padding-left:6px;color:#999}
.newsletter .btn{margin-top:9px;width:58px;height:20px;line-height:20px}
.popular{top:177px;height:233px;border-top:0}
.popular .head{height:19px;background:#6d6d6d;color:#fff;text-align:center;font:400 11px/19px "Roboto Condensed",sans-serif}
.tabs{display:flex;height:24px;background:var(--gold);font:400 8px/24px "Roboto Condensed",sans-serif;color:var(--navy)}
.tabs span{flex:1;text-align:center}
.tabs span.on{background:var(--navy);color:#fff;flex:0 0 54px;position:relative}
.tabs span.on:after{content:"";position:absolute;left:23px;bottom:-5px;border:5px solid transparent;border-bottom:0;border-top-color:var(--navy)}
.pop-item{position:absolute;left:8px;display:flex;gap:11px;align-items:center}
.pop-item .pic{width:46px;height:46px;border:1px solid #ddd}
.pop-item em{font:italic 700 7px/11px "Lato",sans-serif;color:#333;width:100px}
.view-all{position:absolute;right:9px;top:219px;font:400 8px/10px "Roboto Condensed",sans-serif;color:var(--navy);text-decoration:underline}
.follow{top:428px;height:64px;padding:8px;border-top:4px solid #ddd;border-bottom:4px solid #ddd}
.socials{display:flex;gap:12px;margin-top:6px}
.socials span{width:22px;height:22px;border-radius:2px}
.archives{top:510px;height:137px;padding:8px 9px}
.archives ul{list-style:none;margin-top:5px}
.archives li{font:700 7px/14.8px "Lato",sans-serif;color:#444;border-bottom:1px solid #eee}
.archives li:last-child{border:0}
.tags{top:665px;height:107px;padding:6px 8px}
.tag-list{display:flex;flex-wrap:wrap;gap:7px 3px;margin-top:6px}
.tag-list span{background:var(--gold);color:var(--navy);font:400 9px/19px "Roboto Condensed",sans-serif;height:19px;padding:0 12px}
.ad{position:absolute;left:450px;top:790px;width:173px;height:152px;background:linear-gradient(160deg,#4a3a48 0%,#6b4d3a 45%,#1c1a1c 100%)}

/* about */
.about{position:absolute;left:0;top:964px;width:700px;height:209px;overflow:hidden}
.about .bg{position:absolute;inset:0;background:linear-gradient(180deg,#5b6888 0%,#46577c 60%,#3a4a6c 100%)}
.about .portrait{position:absolute;left:77px;top:28px;width:157px;height:158px;border:3px solid #cfd3dc;background:linear-gradient(180deg,#c9d8e6,#8aa3bd)}
.about h2{position:absolute;left:256px;top:27px;font:400 16px/20px "Roboto Condensed",sans-serif;color:var(--gold)}
.about p{position:absolute;left:256px;top:60px;width:368px;font:400 7.8px/12.2px "Lato",sans-serif;color:#fff}
.about .btn{position:absolute;left:256px;top:158px;width:59px;height:24px;line-height:24px;font-size:10px}
.site-footer{position:absolute;left:0;top:1173px;width:700px;height:27px;background:var(--navy-dark);color:#fff;text-align:center;font:400 7.5px/27px "Roboto Condensed",sans-serif}
</style>
</head>
<body>

<header class="site-header">
  <div class="brand">Tandem K</div>
  <nav class="nav">
    <a class="active" href="#" style="left:326px">About Me</a>
    <a href="#" style="left:401px">Recent Blog</a>
    <a href="#" style="left:479px">Reader Comments</a>
    <a href="#" style="left:581px">Contact Us</a>
  </nav>
</header>

<div class="section-bar">Recent Blog Posts
  <svg width="12" height="11" viewBox="0 0 12 11"><rect x="1" y="1" width="9" height="9" fill="none" stroke="#f4b41a" stroke-width="1.2"/><path d="M3 4h5M3 6h5M3 8h3" stroke="#f4b41a"/></svg>
</div>

<article class="post" style="top:98px">
  <div class="thumb" role="img" aria-label="Woman with arms open under a bright blue sky" style="background:linear-gradient(160deg,#cfe6f7,#5e9bd0 60%,#b36a9b)"></div>
  <h2>Lorem ipsum dolor sit amet consecit dolor</h2>
  <div class="meta"><span class="dot"></span>June 18, 2016<span class="sep"></span><span class="bubble"></span>No Comments</div>
  <p>Lorem ipsum dolor sit amet, consecit adipiscing elit, sed do eiusmod tempor incidimen labore n dolorme laboris ni ut ullamco Neque porro quisquam est, qui dolorem ipsum</p>
  <div class="share">Share <svg width="10" height="8" viewBox="0 0 10 8"><path d="M1 7C2 3 5 2 7 2V0l3 3-3 3V4C5 4 3 5 1 7z" fill="#f4b41a"/></svg></div>
  <div class="counts"><div class="count c1"><b>560</b><i>Like</i></div><div class="count c2"><b>36</b><i>Plus</i></div><div class="count c3"><b>456</b><i>Post</i></div><div class="count c4"><b>1066</b><i>Email</i></div></div>
  <span class="btn">Read More</span>
</article>

<article class="post" style="top:263px">
  <div class="thumb" role="img" aria-label="Young woman on a sunny beach" style="background:linear-gradient(160deg,#dfe9ef,#e7c4a9 55%,#c9a58a)"></div>
  <h2>Lorem ipsum dolor sit amet consecit dolor</h2>
  <div class="meta"><span class="dot"></span>June 22, 2016<span class="sep"></span><span class="bubble"></span>No Comments</div>
  <p>Lorem ipsum dolor sit amet, consecit adipiscing elit, sed do eiusmod tempor incidimen labore n dolorme laboris ni ut ullamco Neque porro quisquam est, qui dolorem ipsum</p>
  <div class="share">Share <svg width="10" height="8" viewBox="0 0 10 8"><path d="M1 7C2 3 5 2 7 2V0l3 3-3 3V4C5 4 3 5 1 7z" fill="#f4b41a"/></svg></div>
  <div class="counts"><div class="count c1"><b>560</b><i>Like</i></div><div class="count c2"><b>36</b><i>Plus</i></div><div class="count c3"><b>456</b><i>Post</i></div><div class="count c4"><b>1066</b><i>Email</i></div></div>
  <span class="btn">Read More</span>
</article>

<article class="post" style="top:428px">
  <div class="thumb" role="img" aria-label="Black and white photo of a smiling couple" style="background:linear-gradient(135deg,#1a1a1a,#6e6e6e 55%,#d6d6d6)"></div>
  <h2>Lorem ipsum dolor sit amet consecit dolor</h2>
  <div class="meta"><span class="dot"></span>June 26, 2016<span class="sep"></span><span class="bubble"></span>No Comments</div>
  <p>Lorem ipsum dolor sit amet, consecit adipiscing elit, sed do eiusmod tempor incidimen labore n dolorme laboris ni ut ullamco Neque porro quisquam est, qui dolorem ipsum</p>
  <div class="share">Share <svg width="10" height="8" viewBox="0 0 10 8"><path d="M1 7C2 3 5 2 7 2V0l3 3-3 3V4C5 4 3 5 1 7z" fill="#f4b41a"/></svg></div>
  <div class="counts"><div class="count c1"><b>560</b><i>Like</i></div><div class="count c2"><b>36</b><i>Plus</i></div><div class="count c3"><b>456</b><i>Post</i></div><div class="count c4"><b>1066</b><i>Email</i></div></div>
  <span class="btn">Read More</span>
</article>

<article class="post" style="top:593px">
  <div class="thumb" role="img" aria-label="Family playing in a field of red poppies" style="background:linear-gradient(180deg,#a9d4f2,#dfeef8 45%,#6e8f3a 75%,#c8452d)"></div>
  <h2>Lorem ipsum dolor sit amet consecit dolor</h2>
  <div class="meta"><span class="dot"></span>June 30, 2016<span class="sep"></span><span class="bubble"></span>No Comments</div>
  <p>Lorem ipsum dolor sit amet, consecit adipiscing elit, sed do eiusmod tempor incidimen labore n dolorme laboris ni ut ullamco Neque porro quisquam est, qui dolorem ipsum</p>
  <div class="share">Share <svg width="10" height="8" viewBox="0 0 10 8"><path d="M1 7C2 3 5 2 7 2V0l3 3-3 3V4C5 4 3 5 1 7z" fill="#f4b41a"/></svg></div>
  <div class="counts"><div class="count c1"><b>560</b><i>Like</i></div><div class="count c2"><b>36</b><i>Plus</i></div><div class="count c3"><b>456</b><i>Post</i></div><div class="count c4"><b>1066</b><i>Email</i></div></div>
  <span class="btn">Read More</span>
</article>

<article class="post" style="top:759px">
  <div class="thumb" role="img" aria-label="Man with arms spread on the deck of a sailboat at sea" style="background:linear-gradient(180deg,#d9e6f1,#9fb9d3 45%,#3f6590 70%,#e9ecef)"></div>
  <h2>Lorem ipsum dolor sit amet consecit dolor</h2>
  <div class="meta"><span class="dot"></span>July 01, 2016<span class="sep"></span><span class="bubble"></span>No Comments</div>
  <p>Lorem ipsum dolor sit amet, consecit adipiscing elit, sed do eiusmod tempor incidimen labore n dolorme laboris ni ut ullamco Neque porro quisquam est, qui dolorem ipsum</p>
  <div class="share">Share <svg width="10" height="8" viewBox="0 0 10 8"><path d="M1 7C2 3 5 2 7 2V0l3 3-3 3V4C5 4 3 5 1 7z" fill="#f4b41a"/></svg></div>
  <div class="counts"><div class="count c1"><b>560</b><i>Like</i></div><div class="count c2"><b>36</b><i>Plus</i></div><div class="count c3"><b>456</b><i>Post</i></div><div class="count c4"><b>1066</b><i>Email</i></div></div>
  <span class="btn">Read More</span>
</article>

<div class="load-more"><svg width="10" height="10" viewBox="0 0 10 10"><g stroke="#253a5e" stroke-width="1.3"><path d="M5 0v3M5 7v3M0 5h3M7 5h3M1.5 1.5l2 2M6.5 6.5l2 2M8.5 1.5l-2 2M3.5 6.5l-2 2"/></g></svg>Load More Blogs</div>

<aside>
  <section class="widget newsletter">
    <h3>Sign Up For Free Newsletter</h3>
    <div class="field">Enter Your Email Address</div>
    <span class="btn">SUBSCRIBE</span>
  </section>

  <section class="widget popular">
    <div class="head">Popular</div>
    <div class="tabs"><span class="on">Page Views</span><span>Social Shares#</span><span>Comments</span></div>
    <div class="pop-item" style="top:61px"><div class="pic" role="img" aria-label="Woman in a green meadow" style="background:linear-gradient(160deg,#e8efd2,#7e9a45)"></div><em>Lorem ipsum dolor sit ame consectetuer adipiscing Dolor sit almet</em></div>
    <div class="pop-item" style="top:112px"><div class="pic" role="img" aria-label="Woman in white dress in a field" style="background:linear-gradient(160deg,#f1f5e8,#9cb46a)"></div><em>Lorem ipsum dolor sit ame consectetuer adipiscing Dolor sit almet</em></div>
    <div class="pop-item" style="top:163px"><div class="pic" role="img" aria-label="Portrait of a smiling man" style="background:linear-gradient(160deg,#e6e6e6,#9a8a7c)"></div><em>Lorem ipsum dolor sit ame consectetuer adipiscing</em></div>
    <span class="view-all">View All &gt;&gt;</span>
  </section>

  <section class="widget follow">
    <h3>Follow Us</h3>
    <div class="socials">
      <span style="background:#1b75bb"></span><span style="background:#e4473b"></span><span style="background:#27a9e1"></span><span style="background:#c4302b"></span><span style="background:#1f5e8f"></span>
    </div>
  </section>

  <section class="widget archives">
    <h3>Archives</h3>
    <ul><li>July 2016</li><li>June 2016</li><li>May 2016</li><li>April 2016</li><li>March 2016</li><li>February 2016</li><li>January 2016</li></ul>
  </section>

  <section class="widget tags">
    <h3>Popular Tags</h3>
    <div class="tag-list"><span>SIT</span><span>DOLOR</span><span>ALMETSIT</span><span>DOLOR</span><span>ELIT</span><span>SIT</span><span>ELIT</span><span>ALMETS</span></div>
  </section>

  <div class="ad" role="img" aria-label="Advertisement: pickup truck at dusk"></div>
</aside>

<section class="about">
  <div class="bg" role="img" aria-label="Soft blue beach scene at dusk"></div>
  <div class="portrait" role="img" aria-label="Portrait of the author"></div>
  <h2>About Me</h2>
  <p>Lorem ipsum dolor sit amet, consectetuer adipiscing elit, sed diam nonummy nibh euismod alme tincidunt ut laoreet dolore magna aliquam erat volutpat. Ut wisi enim ad minim veniam, quis dol nostrud exerci tation ullamcorper suscipit lobortis nisl ut aliquip ex ea commodo consequat list Duis autem vel eum iriure dolor in hendrerit in vulputate velit esse molestie consequat, vel alm illum dolore eu feugiat nulla facilisis at vero eros et accumsan et iusto odio dignissim qui blandit illum dolore eu feugiat nulla facilisis at vero eros et accumsan et iusto odio dignissim qui blandit praesent luptatum zzril delenit augue duis dolore te feugait nulla facilisi.</p>
  <span class="btn">Read More</span>
</section>

<footer class="site-footer">© 2016 Tandem K. All Rights Reserved.</footer>

</body>
</html>
```